Quintara Legal Group Letterhead

Need a new letterhead for my law firm.
IDENTIFYING INFORMATION BELOW:
Anselmo R Quintara III
Attorney at Law
Address: 2847 Larkspur Blvd, Ste 300, Dallas, TX 75204
Phone: 877-482-6017
Fax: 469-738-1452
Email: bry@bry7legal.example
Website: www.bry7legal.example

Colors
0054AA
0677BA
7BADD7
CADEEF
E8F1F8

Requirements
Must have
• Logo needs to be on the letterhead, along with identifying information which is included in the project description.

```html
<!DOCTYPE html>
<html lang="en">
<head>
<meta charset="utf-8">
<title>Quintara Legal Group Letterhead</title>
<link href="https://fonts.googleapis.com/css2?family=Roboto:wght@300;400;700&family=Pinyon+Script&display=swap" rel="stylesheet">
<style>
  :root {
    --brand-blue: #0054AA;
    --brand-blue-mid: #0677BA;
    --ink: #1a1a1a;
    --ink-soft: #2a2a2a;
    --rule: #9a9a9a;
    --paper: #f3f3f3;
    --paper-shade: #ececec;
    --backdrop: #e4e4e4;
    --black-band: #050505;
  }
  * { margin: 0; padding: 0; box-sizing: border-box; }
  html, body {
    width: 1200px; height: 1200px; overflow: hidden;
    background: var(--backdrop);
    font-family: "Roboto", Arial, sans-serif;
  }
  .letterhead {
    position: absolute; left: 203px; top: 40px;
    width: 793px; height: 1120px;
    background: linear-gradient(160deg, var(--paper) 0%, #f6f6f6 45%, var(--paper-shade) 100%);
    color: var(--ink);
    overflow: hidden;
  }
  .brand {
    position: absolute; top: 62px; left: 0; width: 100%;
    text-align: center;
  }
  .brand-name {
    font-weight: 700; font-size: 30px; line-height: 32px;
    letter-spacing: 2px; color: var(--ink);
  }
  .brand-tagline {
    margin-top: 4px;
    font-weight: 400; font-size: 14px; letter-spacing: 2.4px;
    color: var(--ink);
  }
  .letter {
    position: absolute; left: 85px; top: 262px; width: 623px;
    font-weight: 300; font-size: 13px; line-height: 18.6px;
    color: var(--ink-soft);
  }
  .letter-date { margin-bottom: 19px; }
  .letter-recipient { margin-bottom: 37px; }
  .letter-salutation { margin-bottom: 19px; }
  .letter-body p { text-align: justify; margin-bottom: 18.6px; }
  .letter-closing { margin-top: 45px; }
  .letter-signature {
    font-family: "Pinyon Script", cursive;
    font-size: 25px; line-height: 32px; margin-top: 4px;
    color: var(--ink);
  }
  .footer-contact {
    position: absolute; left: 55px; top: 1013px;
    display: flex; font-size: 13.3px; line-height: 16px; color: var(--ink);
  }
  .attorney { padding-right: 16px; border-right: 1px solid var(--rule); }
  .attorney-name { color: var(--brand-blue); font-weight: 700; }
  .channels { padding-left: 20px; }
  .channel { display: flex; align-items: center; }
  .channel svg { width: 10px; height: 10px; margin-right: 8px; flex: none; }
  .base-band { position: absolute; left: 0; bottom: 0; width: 793px; height: 32px; }
</style>
</head>
<body>
  <main class="letterhead">
    <header class="brand">
      <div class="brand-name">QUINTARA LEGAL GROUP</div>
      <div class="brand-tagline">STEADFAST ADVOCACY</div>
    </header>

    <article class="letter">
      <p class="letter-date">01 January 2050</p>
      <p class="letter-recipient">Company (Pvt) Ltd.<br>PO Box 3355 Mainville St<br>Sample City Country 3355</p>
      <p class="letter-salutation">Dear Dorian Halvek,</p>
      <div class="letter-body">
        <p>Lorem ipsum dolor sit amet, consectetuer adipiscing elit, sed diam nonummy nibh euismod tincidunt ut laoreet dolore magna aliquam erat volutpat. Ut wisi enim ad minim veniam, quis nostrud exerci tation ullamcorper suscipit lobortis nisl ut aliquip ex ea commodo consequat. Duis dolore te feugait nulla facilisi. Nam liber tempor cum soluta nobis eleifend option congue nihil imperdiet doming id quod mazim placerat facer possim assum. Lorem ipsum dolor sit amet, consectetuer adipiscing elit, sed diam nonummy nibh euismod tincidunt ut laoreet dolore magna aliquam erat volutpat. Ut wisi enim ad minim veniam, quis nostrud exerci tation ullamcorper suscipit lobortis nisl ut aliquip ex ea commodo consequat.</p>
        <p>Consectetuer adipiscing elit, sed diam nonummy nibh euismod tincidunt ut laoreet dolore magna aliquam erat volutpat. Ut wisi enim ad minim veniam, quis nostrud exerci tation ullamcorper suscipit lobortis nisl ut aliquip ex ea commodo consequat. Consectetuer adipiscing elit, sed diam nonummy nibh euismod tincidunt ut laoreet dolore magna aliquam erat volutpat. Ut wisi enim ad minim veniam, quis nostrud exerci tation ullamcorper suscipit lobortis nisl ut aliquip ex ea commodo consequat.</p>
        <p>Consectetuer adipiscing elit, sed diam nonummy nibh euismod tincidunt ut laoreet dolore magna aliquam erat volutpat. Ut wisi enim ad minim veniam, quis nostrud exerci tation ullamcorper suscipit lobortis nisl ut aliquip ex ea commodo consequat. Consectetuer adipiscing elit, sed diam nonummy nibh euismod tincidunt ut laoreet dolore magna aliquam erat volutpat. Ut wisi enim ad minim veniam, quis nostrud exerci tation ullamcorper suscipit lobortis nisl ut aliquip ex ea commodo consequat.</p>
      </div>
      <p class="letter-closing">Sincerely Yours</p>
      <p class="letter-signature">Casimir Oldenfeld</p>
    </article>

    <footer class="footer-contact">
      <div class="attorney">
        <div class="attorney-name">Anselmo R Quintara III</div>
        <div>Attorney at Law</div>
        <div>2847 Larkspur Blvd</div>
        <div>Ste 300, Dallas, TX 75204</div>
      </div>
      <div class="channels">
        <div class="channel">
          <svg viewBox="0 0 10 10" aria-hidden="true"><path fill="#0054AA" d="M2 0.5 L3.6 2.6 L2.8 3.6 Q3.8 5.8 6.2 7 L7.2 6.2 L9.5 7.8 L8.6 9.4 Q4.5 9.5 1.6 5.6 Q0.2 3.2 0.6 1.2 Z"/></svg>
          <span>877-482-6017</span>
        </div>
        <div class="channel">
          <svg viewBox="0 0 10 10" aria-hidden="true"><rect fill="#0054AA" x="2.5" y="0.5" width="5" height="2.5"/><rect fill="#0054AA" x="0.5" y="3.5" width="9" height="4" rx="0.6"/><rect x="2.5" y="6.5" width="5" height="3" fill="#fff" stroke="#0054AA" stroke-width="1"/></svg>
          <span>469-738-1452</span>
        </div>
        <div class="channel">
          <svg viewBox="0 0 10 10" aria-hidden="true"><rect fill="#0054AA" x="0.5" y="2" width="9" height="6"/><path d="M0.8 2.3 L5 5.6 L9.2 2.3" fill="none" stroke="#fff" stroke-width="0.9"/></svg>
          <span>bry@bry7legal.example</span>
        </div>
        <div class="channel">
          <svg viewBox="0 0 10 10" aria-hidden="true"><g fill="none" stroke="#0054AA" stroke-width="1"><circle cx="5" cy="5" r="4.3"/><path d="M0.7 5 H9.3 M5 0.7 V9.3 M5 0.7 Q2.3 5 5 9.3 M5 0.7 Q7.7 5 5 9.3"/></g></svg>
          <span>www.bry7legal.example</span>
        </div>
      </div>
    </footer>

    <svg class="base-band" viewBox="0 0 793 32" aria-hidden="true">
      <polygon points="0,19 502,19 494,32 0,32" fill="#0054AA"/>
      <polygon points="520,0 793,0 793,32 495,32" fill="#050505"/>
    </svg>
  </main>
</body>
</html>
```